Veldmark Supplies Business Card

Professional business card that stand out to our potential customers. Front and back with clean modern design

Industry/Entity Type

Oil and gas

Contact Information for Business Card

Name, address, website , office phone and cell number

Requirements
Must have
• Editable files for each employee

```html
<!DOCTYPE html>
<html lang="en">
<head>
<meta charset="utf-8">
<title>Veldmark Supplies Business Card</title>
<link href="https://fonts.googleapis.com/css2?family=Montserrat:wght@400;500;700;800&display=swap" rel="stylesheet">
<style>
  :root {
    --backdrop: #2a2a2c;
    --cyan: #0eaed1;
    --red: #ec2027;
    --white: #ffffff;
    --card-w: 665px;
    --card-h: 380px;
  }
  * { margin: 0; padding: 0; box-sizing: border-box; }
  html, body {
    width: 1200px; height: 880px; overflow: hidden;
    background: var(--backdrop);
    font-family: "Montserrat", Arial, sans-serif;
  }
  .canvas {
    width: 1200px; height: 880px;
    display: flex; flex-direction: column; align-items: center; justify-content: center;
    gap: 40px;
  }
  .card {
    position: relative;
    width: var(--card-w); height: var(--card-h);
    overflow: hidden;
    box-shadow: 0 10px 28px rgba(0,0,0,0.45);
  }
  /* front */
  .card-front {
    background: var(--cyan);
    display: flex; align-items: center; justify-content: center;
  }
  .brand {
    display: flex; align-items: center; gap: 14px;
    font-weight: 800; text-transform: uppercase; letter-spacing: 0.04em;
    white-space: nowrap;
  }
  .brand-square { display: block; background: var(--white); flex: none; }
  .card-front .brand { color: var(--white); font-size: 40px; }
  .card-front .brand-square { width: 34px; height: 34px; }
  /* back */
  .card-back { background: var(--white); }
  .back-wave { position: absolute; inset: 0; }
  .card-back .brand {
    position: absolute; left: 40px; top: 112px;
    color: var(--red); font-size: 19px; gap: 9px;
  }
  .card-back .brand-square { width: 18px; height: 18px; background: var(--red); }
  .contact {
    position: absolute; right: 22px; top: 70px;
    color: var(--white); text-align: right;
    font-size: 14px; line-height: 1.55;
  }
  .contact-name { font-weight: 700; font-size: 16px; letter-spacing: 0.02em; }
  .contact-title { margin-bottom: 12px; }
  .contact-address { margin-bottom: 10px; }
  .contact-line { display: flex; align-items: center; justify-content: flex-end; gap: 10px; height: 24px; }
  .icon { width: 20px; height: 20px; background: var(--red); border-radius: 3px; display: flex; align-items: center; justify-content: center; }
</style>
</head>
<body>
<main class="canvas">
  <section class="card card-front">
    <div class="brand"><span class="brand-square"></span>Veldmark Supplies</div>
  </section>

  <section class="card card-back">
    <svg class="back-wave" viewBox="0 0 665 380" width="665" height="380" aria-hidden="true">
      <path d="M0 310 C250 300 330 240 400 150 S530 0 600 0 L665 0 L665 380 L0 380 Z" fill="#0eaed1"/>
      <path d="M0 304 C245 294 322 234 392 146 S522 -6 592 -6" fill="none" stroke="#ffffff" stroke-width="8"/>
      <path d="M0 296 C240 286 315 228 384 140 S514 -10 584 -10" fill="none" stroke="#ec2027" stroke-width="10"/>
      <path d="M0 286 C235 276 306 220 374 132 S504 -14 574 -14" fill="none" stroke="#ffffff" stroke-width="6"/>
      <path d="M0 280 C230 270 300 214 368 126 S498 -18 568 -18" fill="none" stroke="#0eaed1" stroke-width="5"/>
    </svg>

    <div class="brand"><span class="brand-square"></span>Veldmark Supplies</div>

    <div class="contact">
      <div class="contact-name">DANE HOLLOWAY</div>
      <div class="contact-title">President</div>
      <div class="contact-address">482 Harlan Ave, Ste 100,<br>Midvale, TX 75390</div>
      <div class="contact-line"><span>555-214-7730</span>
        <span class="icon"><svg width="12" height="12" viewBox="0 0 12 12"><path d="M2 1 L4 1 L5 4 L3.6 5 C4.3 6.6 5.4 7.7 7 8.4 L8 7 L11 8 L11 10 C11 10.6 10.6 11 10 11 C5 11 1 7 1 2 C1 1.4 1.4 1 2 1 Z" fill="#fff"/></svg></span></div>
      <div class="contact-line"><span>000-000-9999</span>
        <span class="icon"><svg width="12" height="12" viewBox="0 0 12 12"><rect x="3" y="0.8" width="6" height="10.4" rx="1" fill="none" stroke="#fff" stroke-width="1.2"/><circle cx="6" cy="9.5" r="0.7" fill="#fff"/></svg></span></div>
      <div class="contact-line"><span>info@example-youremail.com</span>
        <span class="icon"><svg width="12" height="12" viewBox="0 0 12 12"><rect x="1" y="2.5" width="10" height="7" fill="none" stroke="#fff" stroke-width="1.2"/><path d="M1 2.5 L6 6.5 L11 2.5" fill="none" stroke="#fff" stroke-width="1.2"/></svg></span></div>
      <div class="contact-line"><span>www.example-yourwebsite.com</span>
        <span class="icon"><svg width="12" height="12" viewBox="0 0 12 12"><circle cx="6" cy="6" r="4.8" fill="none" stroke="#fff" stroke-width="1.1"/><ellipse cx="6" cy="6" rx="2" ry="4.8" fill="none" stroke="#fff" stroke-width="1"/><path d="M1.2 6 H10.8" stroke="#fff" stroke-width="1"/></svg></span></div>
    </div>
  </section>
</main>
</body>
</html>
```